Los Brava Dip – CPG Website with WordPress - Store Locator: WP Maps plugin

Larkfield Food Company is a startup consumer packaged goods (CPG) brand launching its flagship product line — Los Brava Dip. We’re seeking a talented web designer to create a bold, professional, mobile-optimized website using WordPress with a WP Maps store locator to help customers find local retailers.

Our goal is to build a strong online presence that supports both retail growth and direct-to-consumer sales.

See Los Brava _Website_Design_Brief word document.

The website URL is https://losbravadip.example/

Target Market(s)

Consumers of gourmet salsa

Industry/Entity Type

Consumer Packaged Goods - Salsa manufacturer.

Coding

Coded - Design and coding required

Number of Pages Required

5+ page

Requirements
Must have
• The design of the Los Brava Dip website shall emulate the clean, polished aesthetic of Fennigo.example.

```html
<!DOCTYPE html>
<html lang="en">
<head>
<meta charset="utf-8">
<title>Los Brava Dip – Home</title>
<link rel="stylesheet" href="https://fonts.googleapis.com/css2?family=Arvo:wght@400;700&family=Nunito+Sans:wght@400;600;700&display=swap">
<style>
:root{
  --red:#cc1f2b;
  --green:#446a2b;
  --star:#7d9a50;
  --yellow:#f0b73a;
  --ink:#111;
  --body:#6b6b6b;
  --white:#fff;
  --line:#dcdcdc;
}
*{margin:0;padding:0;box-sizing:border-box}
html,body{width:1200px;height:3741px;overflow:hidden;background:var(--white)}
body{position:relative;font-family:"Nunito Sans",Arial,sans-serif;color:var(--ink)}
.abs{position:absolute;white-space:nowrap}
.wrap{white-space:normal}
.slab{font-family:"Arvo",Georgia,serif;font-weight:700}
.promo-bar{left:0;top:0;width:1200px;height:38px;background:var(--red);color:var(--white);font-size:14px;text-align:center;line-height:38px}
.site-nav{left:0;top:38px;width:1200px;height:87px;background:var(--white)}
.nav-link{top:30px;font-size:17px;color:var(--ink)}
.nav-link.active{color:var(--red)}
.brand{left:470px;top:18px;width:260px;text-align:center;font-size:38px;color:var(--red);line-height:50px}
.hero{left:0;top:125px;width:1200px;height:599px;background:radial-gradient(ellipse at 50% 55%,#c8512b 0%,#8a3a1f 40%,#4a2e1c 75%,#2f2418 100%)}
.hero-title{left:0;top:195px;width:1200px;text-align:center;font-size:58px;color:var(--white)}
.section-title{left:0;width:1200px;text-align:center;font-size:40px}
.flourish{width:104px;height:6px;left:548px;border-radius:3px}
.product-photo{left:125px;top:910px;width:455px;height:335px;background:linear-gradient(90deg,#c23a2a,#8fae3f 50%,#d0612d);border-radius:40px 40px 20px 20px;opacity:.9}
.product-name{left:642px;top:912px;font-size:30px}
.copy{font-size:15px;line-height:25.7px;color:var(--body);white-space:normal}
.btn{border:2px solid var(--red);border-radius:5px;color:var(--red);font-family:"Arvo",Georgia,serif;font-weight:700;font-size:19px;text-align:center}
.reviews{left:0;top:1340px;width:1200px;height:735px;background:var(--green)}
.panel{background:var(--white);border-radius:8px}
.stars{display:flex;gap:5px}
.star{width:25px;height:25px;background:var(--star);display:flex;align-items:center;justify-content:center}
.stars.sm .star{width:19px;height:19px}
.review-card{top:1672px;width:284px;height:225px;border:1px solid #e6e6e6;border-radius:10px;padding:22px 17px;box-shadow:0 2px 6px rgba(0,0,0,.06);white-space:normal}
.review-card h3{font-size:18px;font-weight:600;line-height:25px;margin:18px 0 10px}
.review-card p{font-size:13.5px;line-height:21.5px;color:#333}
.pager{width:22px;height:22px;border-radius:50%;border:1.5px solid #222}
.recipes{left:0;top:2075px;width:1200px;height:703px;background:var(--yellow)}
.recipe-photo{left:142px;top:2296px;width:320px;height:353px;border-radius:8px;background:linear-gradient(160deg,#a8a29c,#b85f2c 45%,#d58a35 70%,#7a6f66)}
.stat{top:2505px;font-size:16px}
.stat b{font-weight:600;display:block}
.stat span{display:block;margin-top:8px;font-size:15px;color:#333}
.divider{top:2505px;width:1px;height:55px;background:var(--line)}
.social-feed{left:0;top:2778px;width:1200px;height:654px;background:var(--red)}
.tile{top:2986px;width:231px;height:332px}
.circle-arrow{width:28px;height:28px;border:1.5px solid var(--white);border-radius:50%}
.footer-brand{left:108px;top:3505px;font-size:34px;color:var(--red)}
.social-dot{top:3596px;width:32px;height:32px;border-radius:50%;background:var(--red)}
.footer-head{top:3496px;font-size:21px;font-weight:600}
.footer-rule{top:3534px;width:42px;height:2px;background:var(--red)}
.footer-links{top:3553px;font-size:14.5px;line-height:25.7px;list-style:none}
.pay{top:3550px;height:30px;padding:0 6px;border:1px solid var(--line);border-radius:4px;font-size:12px;font-weight:700;line-height:28px;color:#333}
.bottom-rule{left:112px;top:3677px;width:976px;height:1px;background:var(--line)}
.legal{left:0;top:3700px;width:1200px;text-align:center;font-size:15px}
</style>
</head>
<body>

<div class="abs promo-bar slab">FREE SHIPPING INCLUDED &nbsp;|&nbsp; Boxes starting at $20</div>

<header class="abs site-nav">
  <span class="abs nav-link active slab" style="left:110px">Home</span>
  <span class="abs nav-link slab" style="left:181px">Product</span>
  <span class="abs nav-link slab" style="left:267px">Where to Buy</span>
  <span class="abs nav-link slab" style="left:401px">Recipe</span>
  <div class="abs brand slab">Los Brava</div>
  <span class="abs nav-link slab" style="left:783px">About</span>
  <span class="abs nav-link slab" style="left:853px">Review</span>
  <span class="abs nav-link slab" style="left:937px">Contact</span>
  <svg class="abs" style="left:1032px;top:32px" width="18" height="22" viewBox="0 0 18 22"><path d="M2 7h14l-1 15H3z" fill="#cc1f2b"/><path d="M5 8V5a4 4 0 0 1 8 0v3" stroke="#cc1f2b" stroke-width="2" fill="none"/></svg>
  <svg class="abs" style="left:1069px;top:32px" width="20" height="22" viewBox="0 0 20 22"><circle cx="10" cy="6" r="5" fill="#cc1f2b"/><path d="M0 22a10 9 0 0 1 20 0z" fill="#cc1f2b"/></svg>
</header>

<section class="abs hero" role="img" aria-label="Three jars of Los Brava Dip salsa on a table with chilies and tortilla chips"></section>
<h1 class="abs hero-title slab">Spice Up Your Meals!</h1>

<h2 class="abs section-title slab" style="top:792px">Featured Product</h2>
<div class="abs flourish" role="img" aria-label="Red swirl divider" style="top:864px;background:var(--red)"></div>
<div class="abs product-photo" role="img" aria-label="Habanero, Verde and All Natural jars of Los Brava Dip"></div>
<h3 class="abs product-name slab">Los Brava Dip</h3>
<p class="abs copy" style="left:642px;top:961px;width:448px">Lorem ipsum dolor sit amet, consectetur adipiscing elit, sed do eiusmod tempor incididunt ut labore et dolore magna aliqua. Ut enim ad minim veniam, quis nostrud exercitation ullamco laboris nisi ut aliquip ex ea commodo consequat. Duis aute irure dolor in reprehenderit in voluptate velit esse cillum dolore eu fugiat nulla pariatur. Excepteur sint occaecat cupidatat non proident, sunt in culpa qui officia deserunt mollit anim id est laborum.</p>
<div class="abs btn" style="left:640px;top:1166px;width:108px;height:48px;line-height:44px">Shop</div>

<section class="abs reviews"></section>
<h2 class="abs section-title slab" style="top:1417px;color:var(--white)">Reviews</h2>
<div class="abs flourish" role="img" aria-label="Red swirl divider" style="top:1482px;background:var(--red)"></div>
<div class="abs panel" style="left:112px;top:1527px;width:976px;height:450px"></div>
<h3 class="abs slab" style="left:161px;top:1551px;font-size:25px">Let customers speak for us</h3>
<div class="abs stars" style="left:161px;top:1596px">
  <div class="star"><svg width="15" height="15" viewBox="0 0 10 10"><path d="M5 .5l1.4 2.9 3.1.4-2.3 2.2.6 3.1L5 7.6 2.2 9.1l.6-3.1L.5 3.8l3.1-.4z" fill="#fff"/></svg></div>
  <div class="star"><svg width="15" height="15" viewBox="0 0 10 10"><path d="M5 .5l1.4 2.9 3.1.4-2.3 2.2.6 3.1L5 7.6 2.2 9.1l.6-3.1L.5 3.8l3.1-.4z" fill="#fff"/></svg></div>
  <div class="star"><svg width="15" height="15" viewBox="0 0 10 10"><path d="M5 .5l1.4 2.9 3.1.4-2.3 2.2.6 3.1L5 7.6 2.2 9.1l.6-3.1L.5 3.8l3.1-.4z" fill="#fff"/></svg></div>
  <div class="star"><svg width="15" height="15" viewBox="0 0 10 10"><path d="M5 .5l1.4 2.9 3.1.4-2.3 2.2.6 3.1L5 7.6 2.2 9.1l.6-3.1L.5 3.8l3.1-.4z" fill="#fff"/></svg></div>
  <div class="star" style="background:linear-gradient(90deg,var(--star) 50%,#bbb 50%)"><svg width="15" height="15" viewBox="0 0 10 10"><path d="M5 .5l1.4 2.9 3.1.4-2.3 2.2.6 3.1L5 7.6 2.2 9.1l.6-3.1L.5 3.8l3.1-.4z" fill="#fff"/></svg></div>
</div>
<p class="abs" style="left:161px;top:1631px;font-size:17px">from 338 reviews</p>

<article class="abs review-card" style="left:159px">
  <div class="stars sm"><div class="star"><svg width="12" height="12" viewBox="0 0 10 10"><path d="M5 .5l1.4 2.9 3.1.4-2.3 2.2.6 3.1L5 7.6 2.2 9.1l.6-3.1L.5 3.8l3.1-.4z" fill="#fff"/></svg></div><div class="star"><svg width="12" height="12" viewBox="0 0 10 10"><path d="M5 .5l1.4 2.9 3.1.4-2.3 2.2.6 3.1L5 7.6 2.2 9.1l.6-3.1L.5 3.8l3.1-.4z" fill="#fff"/></svg></div><div class="star"><svg width="12" height="12" viewBox="0 0 10 10"><path d="M5 .5l1.4 2.9 3.1.4-2.3 2.2.6 3.1L5 7.6 2.2 9.1l.6-3.1L.5 3.8l3.1-.4z" fill="#fff"/></svg></div><div class="star"><svg width="12" height="12" viewBox="0 0 10 10"><path d="M5 .5l1.4 2.9 3.1.4-2.3 2.2.6 3.1L5 7.6 2.2 9.1l.6-3.1L.5 3.8l3.1-.4z" fill="#fff"/></svg></div><div class="star"><svg width="12" height="12" viewBox="0 0 10 10"><path d="M5 .5l1.4 2.9 3.1.4-2.3 2.2.6 3.1L5 7.6 2.2 9.1l.6-3.1L.5 3.8l3.1-.4z" fill="#fff"/></svg></div></div>
  <h3>Very good, and I’m a salsa snob!</h3>
  <p>In June 2025, Los Brava Dip was put to the test in a blind taste challenge conducted by a third party with 38 participants.</p>
</article>
<article class="abs review-card" style="left:461px">
  <div class="stars sm"><div class="star"><svg width="12" height="12" viewBox="0 0 10 10"><path d="M5 .5l1.4 2.9 3.1.4-2.3 2.2.6 3.1L5 7.6 2.2 9.1l.6-3.1L.5 3.8l3.1-.4z" fill="#fff"/></svg></div><div class="star"><svg width="12" height="12" viewBox="0 0 10 10"><path d="M5 .5l1.4 2.9 3.1.4-2.3 2.2.6 3.1L5 7.6 2.2 9.1l.6-3.1L.5 3.8l3.1-.4z" fill="#fff"/></svg></div><div class="star"><svg width="12" height="12" viewBox="0 0 10 10"><path d="M5 .5l1.4 2.9 3.1.4-2.3 2.2.6 3.1L5 7.6 2.2 9.1l.6-3.1L.5 3.8l3.1-.4z" fill="#fff"/></svg></div><div class="star"><svg width="12" height="12" viewBox="0 0 10 10"><path d="M5 .5l1.4 2.9 3.1.4-2.3 2.2.6 3.1L5 7.6 2.2 9.1l.6-3.1L.5 3.8l3.1-.4z" fill="#fff"/></svg></div><div class="star"><svg width="12" height="12" viewBox="0 0 10 10"><path d="M5 .5l1.4 2.9 3.1.4-2.3 2.2.6 3.1L5 7.6 2.2 9.1l.6-3.1L.5 3.8l3.1-.4z" fill="#fff"/></svg></div></div>
  <h3>Awesome taste, fresh.</h3>
  <p>Very nice overall. I cook a lot so I often make my own, but this is great! Very nice overall. I cook a lot so I often make my own, but this is great!</p>
</article>
<article class="abs review-card" style="left:763px">
  <div class="stars sm"><div class="star"><svg width="12" height="12" viewBox="0 0 10 10"><path d="M5 .5l1.4 2.9 3.1.4-2.3 2.2.6 3.1L5 7.6 2.2 9.1l.6-3.1L.5 3.8l3.1-.4z" fill="#fff"/></svg></div><div class="star"><svg width="12" height="12" viewBox="0 0 10 10"><path d="M5 .5l1.4 2.9 3.1.4-2.3 2.2.6 3.1L5 7.6 2.2 9.1l.6-3.1L.5 3.8l3.1-.4z" fill="#fff"/></svg></div><div class="star"><svg width="12" height="12" viewBox="0 0 10 10"><path d="M5 .5l1.4 2.9 3.1.4-2.3 2.2.6 3.1L5 7.6 2.2 9.1l.6-3.1L.5 3.8l3.1-.4z" fill="#fff"/></svg></div><div class="star"><svg width="12" height="12" viewBox="0 0 10 10"><path d="M5 .5l1.4 2.9 3.1.4-2.3 2.2.6 3.1L5 7.6 2.2 9.1l.6-3.1L.5 3.8l3.1-.4z" fill="#fff"/></svg></div><div class="star"><svg width="12" height="12" viewBox="0 0 10 10"><path d="M5 .5l1.4 2.9 3.1.4-2.3 2.2.6 3.1L5 7.6 2.2 9.1l.6-3.1L.5 3.8l3.1-.4z" fill="#fff"/></svg></div></div>
  <h3>At $4.79 that is a great<br>value.</h3>
  <p>In June 2025, Los Brava Dip was put to the test in a blind taste challenge conducted by a third party with 38 participants.</p>
</article>
<div class="abs pager" style="left:572px;top:1919px;border-color:#ccc"></div>
<div class="abs pager" style="left:606px;top:1919px"></div>

<section class="abs recipes"></section>
<h2 class="abs section-title slab" style="top:2145px;color:var(--red)">Recipes</h2>
<div class="abs flourish" role="img" aria-label="Red swirl divider" style="top:2220px;background:var(--red)"></div>
<div class="abs panel" style="left:112px;top:2262px;width:976px;height:420px"></div>
<div class="abs recipe-photo" role="img" aria-label="Spoonful of Mexican beef and rice with melted cheese"></div>
<h3 class="abs slab" style="left:506px;top:2312px;font-size:27px">One Pot Mexican Beef and Rice</h3>
<p class="abs copy" style="left:506px;top:2355px;width:535px">This One Pot Mexican Beef and Rice is the ultimate weeknight dinner—quick to prepare, easy to clean up, and packed with bold flavor in every bite. Ground beef is browned and simmered with beef broth, sweet corn, and Los Brava Dip, then combined with instant rice and melted cheddar for a hearty, satisfying meal that comes together in just 30 minutes.</p>
<div class="abs stat" style="left:505px"><b>Prep Time:</b><span>10 mins</span></div>
<div class="abs divider" style="left:620px"></div>
<div class="abs stat" style="left:652px"><b>Cook Time:</b><span>20 mins</span></div>
<div class="abs divider" style="left:767px"></div>
<div class="abs stat" style="left:800px"><b>Total Time:</b><span>30 mins</span></div>
<div class="abs divider" style="left:916px"></div>
<div class="abs stat" style="left:947px"><b>Servings:</b><span>46</span></div>
<div class="abs btn" style="left:504px;top:2580px;width:170px;height:48px;line-height:44px">View Recipe</div>

<section class="abs social-feed"></section>
<h2 class="abs section-title slab" style="top:2856px;color:var(--white)">Follow Los Brava Dip on Snapgram</h2>
<div class="abs flourish" role="img" aria-label="White swirl divider" style="top:2930px;background:var(--white)"></div>
<div class="abs tile" role="img" aria-label="Bowls of bean soup topped with tomato" style="left:112px;background:linear-gradient(135deg,#6e5a4e,#5a2b2e 50%,#3aa9a0)"></div>
<div class="abs tile" role="img" aria-label="Plate of cheesy baked dish" style="left:360px;background:linear-gradient(135deg,#2a2d3a,#4c4640 50%,#1f2230)"></div>
<div class="abs" style="left:371px;top:2997px;width:209px;height:300px;border:2px solid var(--yellow);border-radius:6px"></div>
<div class="abs tile" role="img" aria-label="Skillet of chicken enchiladas" style="left:608px;background:linear-gradient(135deg,#dcd6d0,#b0522a 55%,#8a7a70)"></div>
<div class="abs tile" role="img" aria-label="Rice bowl with greens and avocado" style="left:857px;background:linear-gradient(135deg,#6a6a6a,#7f9a4a 45%,#c24a2a 70%,#2f2f2f)"></div>
<div class="abs circle-arrow" style="left:46px;top:3138px"><svg width="26" height="26" viewBox="0 0 26 26"><path d="M15 8l-5 5 5 5" stroke="#fff" stroke-width="1.6" fill="none"/></svg></div>
<div class="abs circle-arrow" style="left:1127px;top:3138px"><svg width="26" height="26" viewBox="0 0 26 26"><path d="M11 8l5 5-5 5" stroke="#fff" stroke-width="1.6" fill="none"/></svg></div>

<footer>
  <div class="abs footer-brand slab">Los Brava</div>
  <div class="abs social-dot" style="left:116px" role="img" aria-label="Chirpbook"></div>
  <div class="abs social-dot" style="left:158px" role="img" aria-label="Snapgram"></div>

  <h4 class="abs footer-head" style="left:327px">Quick Links</h4>
  <div class="abs footer-rule" style="left:327px"></div>
  <ul class="abs footer-links" style="left:327px"><li>Contact Us</li><li>Frequently Asked Questions</li><li>Careers</li></ul>

  <h4 class="abs footer-head" style="left:597px">Other Links</h4>
  <div class="abs footer-rule" style="left:597px"></div>
  <ul class="abs footer-links" style="left:597px"><li>Privacy Policy</li><li>Shipping Policy</li><li>Terms and Conditions</li></ul>

  <span class="abs pay" style="left:822px">Crestcard</span>
  <span class="abs pay" style="left:895px">TapPay</span>
  <span class="abs pay" style="left:955px">Wayfare</span>
  <span class="abs pay" style="left:1018px">Norvia</span>
  <span class="abs pay" style="left:1074px;width:16px;padding:0;border-radius:50%;height:16px;top:3557px;background:#333" aria-label="Ringpay"></span>

  <div class="abs bottom-rule"></div>
  <p class="abs legal">©2025.Larkfield Food Company.All Rights Reserved</p>
</footer>

</body>
</html>
```